SkyvornQ Business Cards and Stationary Design

Need a design for our business cards and stationary. I want to carry on the theme of the logo. I want the business cards to have a design on the back. I would like the business cards and the stationary to carry the same theme, design scheme, and branding

Target Market(s)

Airlines and Maintenance Facilities

Industry/Entity Type

Aviation

Contact Information for Business Card

Name
Position Title
Address: 4827 Trellis Hollow Road, Fort Pierce, Florida, 34951
Office Number
Mobile Number
Email
Website

Font styles to use
Serif
Sans Serif

Colors

Designer to choose colors to be used in the design.

```html
<!DOCTYPE html>
<html lang="en">
<head>
<meta charset="utf-8">
<title>SkyvornQ Business Card</title>
<link rel="stylesheet" href="https://fonts.googleapis.com/css2?family=Open+Sans:wght@400;600;700&display=swap">
<style>
  :root {
    --backdrop: #656565;
    --card: #f4f4f4;
    --navy: #0c2d69;
    --navy-deep: #0a2658;
    --sky: #12a3e6;
    --ink-grey: #4a4a4a;
    --white: #ffffff;
  }
  * { margin: 0; padding: 0; box-sizing: border-box; }
  html, body { width: 1125px; height: 1200px; overflow: hidden; }
  body {
    background: var(--backdrop);
    position: relative;
    font-family: "Open Sans", sans-serif;
  }
  .card {
    position: absolute;
    background: var(--card);
    border-radius: 18px;
    overflow: hidden;
    box-shadow: 0 4px 10px rgba(0,0,0,0.35);
  }
  .card-back { left: 244px; top: 710px; width: 638px; height: 365px; z-index: 1; }
  .card-front { left: 381px; top: 97px; width: 364px; height: 636px; z-index: 2; }

  .brand { position: absolute; left: 0; width: 100%; text-align: center; }
  .brand-dot {
    display: block; margin: 0 auto;
    border: 5px solid var(--sky); border-radius: 50%;
  }
  .brand-name {
    display: block; color: var(--navy); font-weight: 700;
    letter-spacing: 0.2em; padding-left: 0.2em; line-height: 1;
  }
  .card-front .brand { top: 45px; }
  .card-front .brand-dot { width: 96px; height: 96px; }
  .card-front .brand-name { font-size: 34px; margin-top: 20px; }
  .card-back .brand { top: 96px; }
  .card-back .brand-dot { width: 120px; height: 120px; border-width: 6px; }
  .card-back .brand-name { font-size: 42px; margin-top: 22px; }

  .person { position: absolute; top: 276px; width: 100%; text-align: center; }
  .person-name { color: var(--navy); font-weight: 700; font-size: 21px; line-height: 1.2; }
  .person-title { color: var(--ink-grey); font-size: 17px; line-height: 1.4; }

  .contact-list { position: absolute; top: 373px; left: 13px; width: 337px; list-style: none; }
  .contact-row { display: flex; height: 27px; margin-bottom: 3px; }
  .contact-label {
    width: 79px; background: var(--sky); color: var(--white);
    font-size: 16px; text-align: center; line-height: 27px;
    border-radius: 8px 8px 0 0;
  }
  .contact-value {
    flex: 1; margin-left: 2px; background: var(--navy); color: var(--white);
    font-size: 16px; line-height: 27px; padding-left: 6px;
    border-radius: 8px 0 6px 0;
  }

  .footer-band {
    position: absolute; left: 0; bottom: 0; width: 100%; height: 96px;
    background: linear-gradient(180deg, var(--navy) 0%, var(--navy-deep) 100%);
    border-top: 4px solid var(--sky);
  }
  .address {
    position: absolute; left: 30px; top: 575px;
    color: var(--white); font-size: 16px; line-height: 24px;
  }
</style>
</head>
<body>

<section class="card card-back">
  <div class="brand">
    <span class="brand-dot"></span>
    <span class="brand-name">SKYVORNQ</span>
  </div>
</section>

<section class="card card-front">
  <div class="brand">
    <span class="brand-dot"></span>
    <span class="brand-name">SKYVORNQ</span>
  </div>

  <div class="person">
    <p class="person-name">DARA WHITLOW</p>
    <p class="person-title">President and CEO</p>
  </div>

  <ul class="contact-list">
    <li class="contact-row"><span class="contact-label">Phone</span><span class="contact-value">001 555 0148</span></li>
    <li class="contact-row"><span class="contact-label">Mobile</span><span class="contact-value">001 555 0148</span></li>
    <li class="contact-row"><span class="contact-label">Email</span><span class="contact-value">info@skyvornq.com</span></li>
    <li class="contact-row"><span class="contact-label">Website</span><span class="contact-value">www.skyvornq.com</span></li>
  </ul>

  <div class="footer-band" role="img" aria-label="Navy footer band with blue swoosh accent"></div>

  <p class="address">4827 Trellis Hollow Road,<br>Fort Pierce, Florida, 34951</p>
</section>

</body>
</html>
```